Brightway Haus Inc. Business Card Design

Brightway Haus Inc. is in search of a great clean design for our business cards!

Looking to incorporate our full logo and watermark on side one (however, I am open to having the text and watermark separated within the design.)

On side two, I am looking to have contact information (Name, Position, Phone #, Email, Website (www.thebrightwayhaus.ca). Can have the logo and/or watermark as part of the design if applicable.

Please add tagline "Where Shine Counts" on either side 1 or 2. This tagline can be in a sans serif, serif or cursive font as long as it compliments overall design. Capitalization can be title or sentence case depending on how it fits within the design.

Get creative!! Looking for a clean, crisp, premium design! Looking for a glossy card finish with spot UV features when printed. Cards will also be printed with rounded corners. Standard dimensions (3.5 x 2).

Target Market(s)

B2B - primary clients are business owners or property management corporations. (residential jobs are few and far between)

Industry/Entity Type

Business

Contact Information for Business Card

- clean, crisp design
- double sided
- spot UV accents and glossy finish upon printing
- standard business card size (3.5 x 2) with rounded corners
- please see project description for requirements per side

Font styles to use
Sans Serif

Requirements
Must have
• - adequate bleeds with print ready files
• - cohesive design elements between side 1 & 2
• - spot UV elements (can be on both sides or just one, use your discretion)
• - colour pallet should match the logo file provided
• - incorporate tagline "where shine counts" (this tagline can be in a serif or sans serif font as long as it is complimentary to the overall design.
Nice to have
• - Premium elements with a clean design
Should not have
• - Please omit cartoon or whimsical like designs, think premium.
• - Colours should not stray from the pallet of the provided logo.

```html
<!DOCTYPE html>
<html lang="en">
<head>
<meta charset="utf-8">
<title>Brightway Haus Inc. Business Card</title>
<link rel="stylesheet" href="https://fonts.googleapis.com/css2?family=Open+Sans:ital,wght@0,700;0,800;1,400&family=Roboto:wght@400;500;700&display=swap">
<style>
  :root {
    --teal: #0fb8bb;
    --navy: #1a2452;
    --white: #ffffff;
    --paper: #f7f7f5;
    --canvas: #ecebe8;
    --rule: #2b3566;
  }
  * { margin: 0; padding: 0; box-sizing: border-box; }
  html, body { width: 1200px; height: 960px; overflow: hidden; }
  body { background: var(--canvas); font-family: "Roboto", Arial, sans-serif; position: relative; }

  .card { position: absolute; border-radius: 18px; overflow: hidden; }

  /* Side one */
  .card-front { left: 318px; top: 96px; width: 608px; height: 354px; background: var(--paper); }
  .brand-front {
    position: absolute; left: 0; right: 0; top: 156px; text-align: center;
    font-family: "Open Sans", Arial, sans-serif; font-weight: 800; font-size: 36px;
    letter-spacing: -0.5px; color: var(--navy); line-height: 1; white-space: nowrap;
  }
  .brand-mark { display: inline-block; width: 28px; height: 28px; background: var(--teal); vertical-align: -3px; margin-right: 12px; }
  .tagline {
    position: absolute; left: 0; right: 0; top: 288px;
    display: flex; align-items: center; justify-content: center; gap: 8px;
    font-family: "Open Sans", Arial, sans-serif; font-style: italic; font-size: 18px; color: var(--navy);
  }
  .tagline .accent { color: var(--teal); }
  .tagline-rule { width: 104px; height: 1px; background: var(--rule); }

  /* Side two */
  .card-back { left: 320px; top: 493px; width: 600px; height: 342px; background: var(--teal); }
  .card-back svg.backdrop { position: absolute; inset: 0; }
  .brand-back {
    position: absolute; left: 40px; top: 74px;
    font-family: "Open Sans", Arial, sans-serif; font-weight: 800; font-size: 28px;
    letter-spacing: -0.5px; color: var(--white); line-height: 1; white-space: nowrap;
  }
  .brand-back .brand-mark { background: var(--navy); width: 22px; height: 22px; margin-right: 9px; vertical-align: -2px; }
  .person { position: absolute; left: 32px; top: 272px; }
  .person-name { font-weight: 700; font-size: 19px; color: var(--teal); line-height: 20px; }
  .person-role { font-weight: 700; font-size: 14px; color: var(--white); line-height: 18px; }
  .contact-list { position: absolute; right: 40px; top: 194px; list-style: none; text-align: right; color: var(--white); font-size: 14px; }
  .contact-list li { height: 19.4px; line-height: 19.4px; display: flex; justify-content: flex-end; align-items: center; }
  .contact-list svg { width: 14px; height: 14px; margin-left: 8px; flex: none; }
</style>
</head>
<body>

<section class="card card-front" aria-label="Business card side one">
  <div class="brand-front"><span class="brand-mark"></span>BRIGHTWAY HAUS INC.</div>
  <div class="tagline">
    <span class="tagline-rule"></span>
    <span>Where <span class="accent">Shine</span> Counts</span>
    <span class="tagline-rule"></span>
  </div>
</section>

<section class="card card-back" aria-label="Business card side two">
  <svg class="backdrop" width="600" height="342" viewBox="0 0 600 342">
    <path d="M0,200 C150,250 380,150 600,6 L600,342 L0,342 Z" fill="#1a2452"/>
    <path d="M0,198 C150,248 380,148 600,4" fill="none" stroke="#ffffff" stroke-width="5"/>
  </svg>
  <div class="brand-back"><span class="brand-mark"></span>BRIGHTWAY HAUS INC.</div>

  <div class="person">
    <div class="person-name">MARLO VANCE</div>
    <div class="person-role">CEO/FOUNDER</div>
  </div>

  <ul class="contact-list">
    <li>604 555 0182
      <svg viewBox="0 0 14 14"><path d="M3 1 L5.5 1 L6.5 4 L5 5.2 C5.8 7 7 8.2 8.8 9 L10 7.5 L13 8.5 L13 11 C13 12 12 13 11 13 C5.5 13 1 8.5 1 3 C1 2 2 1 3 1 Z" fill="#0fb8bb"/></svg>
    </li>
    <li>604 555 0247
      <svg viewBox="0 0 14 14"><rect x="3.5" y="0.5" width="7" height="13" rx="1.2" fill="none" stroke="#0fb8bb" stroke-width="1.4"/><rect x="6" y="11" width="2" height="1" fill="#0fb8bb"/></svg>
    </li>
    <li>604 555 0319
      <svg viewBox="0 0 14 14"><rect x="4" y="1" width="6" height="4" fill="#0fb8bb"/><rect x="1" y="5" width="12" height="6" rx="1" fill="#0fb8bb"/><rect x="4" y="9" width="6" height="4" fill="#ffffff" stroke="#0fb8bb" stroke-width="1"/></svg>
    </li>
    <li>hello@brightway.ca
      <svg viewBox="0 0 14 14"><rect x="1" y="3" width="12" height="9" fill="#0fb8bb"/><path d="M1 3 L7 8 L13 3" fill="none" stroke="#1a2452" stroke-width="1.2"/></svg>
    </li>
    <li>1420 Harbour Crescent</li>
    <li>Victoria, BC V8W 2T3</li>
  </ul>
</section>

</body>
</html>
```